Quill Petal Loft Hair Salon needs a Webpage design

Quill Petal Loft in Englewood is looking to start their web page, url and business emails, we want to be able to upload pictures and videos on the website. we do blow outs , makeup, color, lash extension, gel manicures

Target Market(s)

everyone

Industry/Entity Type

Beauty Salon

Coding

Coded - Design and coding required

Number of Pages Required

5+ page

Font styles to use
Serif

Colors
ffcf3e
9d9d9d
000000
ffffff

Requirements
Must have
• about us, contact us, products, menu, location, gallery, press
Nice to have
• play video gallery

```html
<!DOCTYPE html>
<html lang="en">
<head>
<meta charset="utf-8">
<title>Quill Petal Loft Hair Salon</title>
<link rel="stylesheet" href="https://fonts.googleapis.com/css2?family=Ubuntu:ital,wght@0,400;0,500;0,700;1,500;1,700&family=Open+Sans:wght@400;600;700&display=swap">
<style>
:root{
  --gold:#f3a704;
  --gold-dark:#d48f00;
  --ink:#111111;
  --text:#555555;
  --grey:#9d9d9d;
  --paper:#ffffff;
  --mist:#efefef;
  --brown:#6b4a1c;
  --pin:#e0443a;
}
*{margin:0;padding:0;box-sizing:border-box}
html,body{width:1200px;height:3509px;overflow:hidden}
body{position:relative;background:var(--paper);font-family:"Open Sans",Arial,sans-serif;color:var(--text)}
.abs{position:absolute}
section,header,footer{position:absolute;left:0;width:1200px}

/* header */
.site-header{top:0;height:136px;z-index:5}
.top-bar{position:absolute;left:0;top:0;width:1200px;height:77px;background:rgba(20,18,18,.85)}
.follow{position:absolute;left:603px;top:28px;color:#fff;font:400 17px "Open Sans",sans-serif;display:flex;align-items:center;gap:10px}
.follow .dot{width:26px;height:26px;border-radius:50%;background:#fff;display:inline-block}
.phone{position:absolute;left:970px;top:27px;color:#fff;font:400 18px "Open Sans",sans-serif;display:flex;align-items:center;gap:10px}
.main-nav{position:absolute;left:281px;top:77px;width:919px;height:45px;background:var(--gold)}
.main-nav a{position:absolute;top:0;height:45px;line-height:45px;color:#fff;text-decoration:none;font:600 13px "Open Sans",sans-serif;letter-spacing:.3px;padding:0 14px;white-space:nowrap}
.main-nav a.active{background:var(--gold-dark)}
.brand{position:absolute;left:0;top:0;width:281px;height:136px;background:#fff;display:flex;align-items:center;justify-content:center;gap:10px;box-shadow:0 2px 6px rgba(0,0,0,.2)}
.brand-mark{width:18px;height:18px;border-radius:50%;background:var(--gold)}
.brand-name{font:500 30px "Ubuntu",sans-serif;color:var(--gold);white-space:nowrap}

/* hero */
.hero{top:0;height:690px;background:linear-gradient(100deg,#5a2b22 0%,#c9a27a 30%,#8a6a4a 50%,#3a2418 75%,#2a1010 100%)}
.hero-title{position:absolute;left:0;width:1200px;top:330px;text-align:center;color:#fff;font:500 54px "Ubuntu",sans-serif;text-shadow:0 2px 6px rgba(0,0,0,.4)}
.hero-sub{position:absolute;left:398px;top:416px;width:437px;height:47px;background:rgba(20,18,18,.7);color:#fff;font:italic 700 25px "Ubuntu",sans-serif;text-align:center;line-height:47px;white-space:nowrap}
.dots{position:absolute;top:636px;left:563px;display:flex;gap:8px}
.dots span{width:11px;height:11px;border-radius:50%;background:#fff}
.dots span.on{background:var(--gold)}

/* services */
.services{top:690px;height:508px;background:var(--gold)}
.section-title{position:absolute;left:0;width:1200px;text-align:center;color:var(--ink);font:700 44px "Ubuntu",sans-serif}
.services .section-title{top:36px}
.rule{position:absolute;left:386px;top:112px;width:631px;height:1px;background:rgba(0,0,0,.25)}
.arrows{position:absolute;left:1022px;top:51px;display:flex;gap:4px}
.arrows span{width:40px;height:34px;background:var(--brown);color:#fff;font:700 16px "Open Sans",sans-serif;display:flex;align-items:center;justify-content:center}
.service{position:absolute;top:182px;width:206px;text-align:center}
.service .photo{width:206px;height:206px;border-radius:50%;border:6px solid var(--ink);box-shadow:inset 0 0 0 5px #fff}
.service .label{margin-top:14px;font:400 32px "Ubuntu",sans-serif;color:var(--ink)}

/* welcome */
.welcome{top:1198px;height:423px;background:#fff}
.welcome h2{position:absolute;left:65px;top:66px;font:500 41px "Ubuntu",sans-serif;color:var(--ink);white-space:nowrap}
.welcome p{position:absolute;left:65px;width:640px;font:400 14.5px/28px "Open Sans",sans-serif;color:var(--text)}
.video{position:absolute;left:746px;top:81px;width:377px;height:263px;background:#000}
.video .still{position:absolute;left:77px;top:6px;width:215px;height:210px;background:linear-gradient(180deg,#cdb79a,#6b4a34)}
.video .play{position:absolute;left:147px;top:85px;width:76px;height:76px;border-radius:50%;background:#fff}
.video .controls{position:absolute;left:0;bottom:0;width:377px;height:34px;background:#111}
.video .track{position:absolute;left:40px;top:16px;width:230px;height:3px;background:#666}

/* gallery */
.gallery{top:1621px;height:741px;background:var(--mist)}
.gallery .section-title{top:42px;font-weight:500;font-size:41px}
.tile{position:absolute;width:339px;height:267px}

/* press */
.press{top:2362px;height:609px;background:#fff}
.press h2{position:absolute;left:73px;top:46px;font:500 50px "Ubuntu",sans-serif;color:var(--ink)}
.story{position:absolute;left:75px;width:680px}
.story h3{font:600 14.5px "Open Sans",sans-serif;color:var(--gold)}
.story .meta{margin-top:8px;font:400 11.5px "Open Sans",sans-serif;color:var(--grey)}
.story p{margin-top:5px;font:600 12.5px/20px "Open Sans",sans-serif;color:#333}
.divider{position:absolute;left:75px;width:680px;height:1px;background:#ddd}
.read-more{position:absolute;left:75px;top:537px;font:400 12px "Open Sans",sans-serif;color:#333}
.social-box{position:absolute;left:823px;top:71px;width:295px;height:467px;border:1px solid #ccc;background:#fff;font-family:"Open Sans",sans-serif;color:#333}
.social-box .head{height:24px;background:#f2f2f2;border-bottom:1px solid #ccc;font:700 11px/24px "Open Sans",sans-serif;padding-left:8px}
.social-box .cover{position:absolute;left:8px;top:34px;width:275px;height:116px;background:linear-gradient(135deg,#8a6a3a,#3a2816)}
.social-box .page{position:absolute;left:70px;top:42px;color:#fff;font:700 15px "Open Sans",sans-serif}
.social-box .likes{position:absolute;left:70px;top:62px;color:#eee;font:400 11px "Open Sans",sans-serif}
.social-box .btn{position:absolute;top:124px;height:20px;background:#f5f5f5;border:1px solid #bbb;font:700 10px/18px "Open Sans",sans-serif;padding:0 8px}
.social-box .small{position:absolute;left:14px;font:400 10px "Open Sans",sans-serif}
.faces{position:absolute;left:14px;top:178px;display:flex;gap:4px}
.faces span{width:26px;height:26px;background:#b89b78}
.post{position:absolute;left:14px;top:218px;width:263px;height:232px;border-top:1px solid #ddd}
.post .avatar{position:absolute;left:0;top:14px;width:42px;height:42px;background:var(--gold)}
.post .txt{position:absolute;left:50px;top:12px;width:210px;font:400 12px/17px "Open Sans",sans-serif}
.post .txt b{color:#3b5998}
.post .caption{position:absolute;left:0;top:110px;width:210px;font:400 12.5px/18px "Open Sans",sans-serif}
.post .pic{position:absolute;left:0;top:155px;width:210px;height:70px;background:linear-gradient(180deg,#c8a88a,#7a5a44)}

/* map */
.location-map{top:2971px;height:215px;background:linear-gradient(135deg,#ecebe6 0%,#e2e0d8 45%,#d7e2cc 60%,#e4e2da 100%)}
.map-pin{position:absolute;left:568px;top:96px}
.map-label{position:absolute;left:594px;top:112px;font:700 11px "Open Sans",sans-serif;color:#333;white-space:nowrap}
.zoom{position:absolute;left:1112px;top:66px;width:22px;height:80px;background:#fff;border:1px solid #bbb;display:flex;flex-direction:column;align-items:center;justify-content:space-around;font:700 13px "Open Sans",sans-serif;color:#555}
.map-thumb{position:absolute;left:36px;top:110px;width:64px;height:64px;background:#4e6a52;border:2px solid #fff}

/* footer */
.site-footer{top:3186px;height:323px;background:var(--gold);color:#222}
.site-footer h4{position:absolute;top:49px;font:500 17px "Ubuntu",sans-serif;color:var(--ink);white-space:nowrap}
.contact-line{position:absolute;left:70px;font:400 12.5px "Open Sans",sans-serif;display:flex;align-items:center;gap:10px;white-space:nowrap}
.foot-social{position:absolute;left:70px;display:flex;gap:6px}
.foot-social span{width:22px;height:22px;border-radius:50%;background:var(--ink)}
.service-list{position:absolute;left:398px;top:90px;list-style:none}
.service-list li{font:600 12px "Open Sans",sans-serif;height:32px;padding-left:14px;position:relative;white-space:nowrap}
.service-list li::before{content:"";position:absolute;left:0;top:7px;width:4px;height:4px;border-radius:50%;background:#222}
.hours{position:absolute;left:590px;top:157px;width:220px;text-align:center;white-space:nowrap}
.hours strong{display:block;font:700 20px "Open Sans",sans-serif;color:var(--ink)}
.hours span{display:block;margin-top:6px;font:400 14px "Open Sans",sans-serif}
.feed{position:absolute;left:940px;top:84px;display:grid;grid-template-columns:repeat(3,59px);gap:9px 8px}
.feed span{height:58px;background:linear-gradient(135deg,#b99a7c,#5a3f2e)}
.feed-btn{position:absolute;left:990px;top:224px;padding:3px 8px;background:#3f6e99;color:#fff;font:600 10px "Open Sans",sans-serif;border-radius:2px;white-space:nowrap}
.foot-rule{position:absolute;left:65px;top:269px;width:1070px;height:1px;background:rgba(0,0,0,.18)}
.copyright{position:absolute;left:0;top:288px;width:1200px;text-align:center;font:400 12px "Open Sans",sans-serif;color:#333}
</style>
</head>
<body>

<section class="hero">
  <div class="abs" style="inset:0" role="img" aria-label="Salon interior with styling chairs, mirrors and a portrait of a model"></div>
  <div class="hero-title">Quill Petal Loft Englewood</div>
  <div class="hero-sub">Full service Hair and Beauty Bar</div>
  <div class="dots"><span class="on"></span><span class="on"></span><span></span><span></span></div>
</section>

<header class="site-header">
  <div class="top-bar">
    <div class="follow">Follow Us on:<span class="dot"></span><span class="dot"></span><span class="dot"></span><span class="dot"></span></div>
    <div class="phone">
      <svg width="20" height="20" viewBox="0 0 24 24"><path fill="#fff" d="M6.6 10.8a15.1 15.1 0 0 0 6.6 6.6l2.2-2.2c.3-.3.7-.4 1-.2 1.1.4 2.3.6 3.6.6.6 0 1 .4 1 1V20c0 .6-.4 1-1 1A17 17 0 0 1 3 4c0-.6.4-1 1-1h3.5c.6 0 1 .4 1 1 0 1.3.2 2.5.6 3.6.1.3 0 .7-.2 1z"/></svg>
      +1 201-555-0148
    </div>
  </div>
  <nav class="main-nav">
    <a class="active" style="left:199px">HOME</a>
    <a style="left:290px">ABOUT US</a>
    <a style="left:397px">PRICES</a>
    <a style="left:489px">GALLERY</a>
    <a style="left:591px">PRODUCTS</a>
    <a style="left:709px">CONTACT US</a>
  </nav>
  <div class="brand"><span class="brand-mark"></span><span class="brand-name">Quill Petal Loft</span></div>
</header>

<section class="services">
  <h2 class="section-title">WHAT WE DO</h2>
  <div class="rule"></div>
  <div class="arrows"><span>&lsaquo;</span><span>&rsaquo;</span></div>
  <div class="service" style="left:98px"><div class="photo" role="img" aria-label="Blow out hairstyle" style="background:radial-gradient(circle,#d9c2a8,#6e5240)"></div><div class="label">Blow Outs</div></div>
  <div class="service" style="left:374px"><div class="photo" role="img" aria-label="Coloured blonde hair" style="background:radial-gradient(circle,#e8d3b4,#8a6a48)"></div><div class="label">Color</div></div>
  <div class="service" style="left:650px"><div class="photo" role="img" aria-label="Haircut service illustration" style="background:radial-gradient(circle,#f7c24a,#d99500)"></div><div class="label">Cuts</div></div>
  <div class="service" style="left:919px"><div class="photo" role="img" aria-label="Braided keratin treated hair" style="background:radial-gradient(circle,#efe6dc,#8a6448)"></div><div class="label">Keratin</div></div>
</section>

<section class="welcome">
  <h2>Welcome to Quill Petal Loft</h2>
  <p style="top:134px">simply dummy text of the printing and typesetting industry. Lorem Ipsum has been the industry's standard dummy text ever since the 1500s, when an unknown printer took a galley of type and scrambled it to make a type specimen book. It has survived not only five centuries, but also the leap into electronic typesetting, remaining essentially unchanged.</p>
  <p style="top:266px">It was popularised in the 1960s with the release of Letraset sheets Contrary to popular belief, Lorem Ipsum is not simply random text. It has roots in a piece of classical Latin literature from 45 BC, making it over 2000 years old.</p>
  <div class="video">
    <div class="still" role="img" aria-label="Video still of a client's styled hair at the salon"></div>
    <div class="play"></div>
    <svg class="abs" style="left:174px;top:108px" width="34" height="30" viewBox="0 0 34 30"><path d="M4 0 L30 15 L4 30 Z" fill="#000"/></svg>
    <div class="controls">
      <svg class="abs" style="left:12px;top:10px" width="12" height="14" viewBox="0 0 12 14"><path d="M0 0 L12 7 L0 14Z" fill="#fff"/></svg>
      <div class="track"></div>
      <svg class="abs" style="left:310px;top:10px" width="16" height="14" viewBox="0 0 16 14"><path d="M0 4h4l5-4v14l-5-4H0z" fill="#fff"/></svg>
      <svg class="abs" style="left:342px;top:10px" width="16" height="14" viewBox="0 0 16 14"><path d="M0 0h5v2H2v3H0zM11 0h5v5h-2V2h-3zM0 9h2v3h3v2H0zM14 9h2v5h-5v-2h3z" fill="#fff"/></svg>
    </div>
  </div>
</section>

<section class="gallery">
  <h2 class="section-title">Our Gallery</h2>
  <div class="tile" style="left:77px;top:136px;background:linear-gradient(135deg,#d8c8b6,#6a4634)" role="img" aria-label="Long wavy brunette hair"></div>
  <div class="tile" style="left:428px;top:136px;background:linear-gradient(135deg,#6a5a52,#1e1816)" role="img" aria-label="Dark glam makeup look"></div>
  <div class="tile" style="left:779px;top:136px;background:linear-gradient(135deg,#a9d4e8,#b08666)" role="img" aria-label="Braided ponytail at the beach"></div>
  <div class="tile" style="left:77px;top:416px;background:linear-gradient(135deg,#e6e0da,#4a2e20)" role="img" aria-label="Elegant updo bun"></div>
  <div class="tile" style="left:428px;top:416px;background:linear-gradient(135deg,#9ab6c4,#d8c4a6)" role="img" aria-label="Blonde braided hairstyle"></div>
  <div class="tile" style="left:779px;top:416px;background:linear-gradient(135deg,#5a7a50,#d6a870)" role="img" aria-label="Voluminous blonde curls"></div>
</section>

<section class="press">
  <h2>Press</h2>
  <article class="story" style="top:127px">
    <h3>Arvo Could Be Shopping Some Assets To Help Relieve Kemra</h3>
    <div class="meta">San Francisco, Aug. 27,2015/NewsWireline/- Quill Petal Loft</div>
    <p>Ultrices proin mi urna nibh ut, aenean sollicitudin etiam libero nisl, ultrices ridiculus in magna purus consequuntur, ipsum donec orci ad vitae pede, id odio. Turpis venenatis at laoreet. Etiam commodo fusce in diam feugiat, ...</p>
  </article>
  <div class="divider" style="top:234px"></div>
  <article class="story" style="top:268px">
    <h3>Arvo Could Be Shopping Some Assets To Help Relieve Kemra</h3>
    <div class="meta">San Francisco, Aug. 27,2015/NewsWireline/- Quill Petal Loft</div>
    <p>Ultrices proin mi urna nibh ut, aenean sollicitudin etiam libero nisl, ultrices ridiculus in magna purus consequuntur, ipsum donec orci ad vitae pede, id odio. Turpis venenatis at laoreet. Etiam commodo fusce in diam feugiat, ...</p>
  </article>
  <div class="divider" style="top:378px"></div>
  <article class="story" style="top:413px">
    <h3>Arvo Could Be Shopping Some Assets To Help Relieve Kemra</h3>
    <div class="meta">San Francisco, Aug. 27,2015/NewsWireline/- Quill Petal Loft</div>
    <p>Ultrices proin mi urna nibh ut, aenean sollicitudin etiam libero nisl, ultrices ridiculus in magna purus consequuntur, ipsum donec orci ad vitae pede, id odio. Turpis venenatis at laoreet. Etiam commodo fusce in diam feugiat, ...</p>
  </article>
  <div class="read-more">Read More &rarr;</div>

  <aside class="social-box">
    <div class="head">Find us on Friendwall</div>
    <div class="cover" role="img" aria-label="Salon page cover photo"></div>
    <div class="abs" style="left:16px;top:42px;width:46px;height:46px;background:#fff"></div>
    <div class="page">Quill Petal Loft</div>
    <div class="likes">15 likes</div>
    <div class="btn" style="left:16px">Like Page</div>
    <div class="btn" style="left:225px">Share</div>
    <div class="small" style="top:160px">Be the first of your friends to like this</div>
    <div class="faces"><span></span><span></span><span></span><span></span><span></span><span></span><span></span></div>
    <div class="post">
      <div class="avatar"></div>
      <div class="txt"><b>Quill Petal Loft</b> added 5 new photos<br>5 hrs &middot; Englewood, NJ</div>
      <div class="caption">Mommy and daughter Glam! Stunning hair and Makeup</div>
      <div class="pic" role="img" aria-label="Recent salon photos"></div>
    </div>
  </aside>
</section>

<section class="location-map">
  <div class="abs" style="inset:0" role="img" aria-label="Street map showing the salon location in Englewood"></div>
  <div class="map-thumb"></div>
  <svg class="map-pin" width="20" height="30" viewBox="0 0 12 18"><path d="M6 0a6 6 0 0 0-6 6c0 4.5 6 12 6 12s6-7.5 6-12a6 6 0 0 0-6-6z" fill="var(--pin)"/><circle cx="6" cy="6" r="2.2" fill="#8a1c16"/></svg>
  <div class="map-label">Quill Petal Loft</div>
  <div class="zoom"><span>+</span><span>&minus;</span></div>
</section>

<footer class="site-footer">
  <h4 style="left:65px">CONTACT US</h4>
  <div class="contact-line" style="top:101px">
    <svg width="12" height="14" viewBox="0 0 12 16"><path d="M6 0a6 6 0 0 0-6 6c0 4.5 6 10 6 10s6-5.5 6-10a6 6 0 0 0-6-6zm0 8.5A2.5 2.5 0 1 1 6 3.5a2.5 2.5 0 0 1 0 5z" fill="#222"/></svg>
    14 Lantern Row Englewood, NJ</div>
  <div class="contact-line" style="top:135px">
    <svg width="12" height="12" viewBox="0 0 24 24"><path fill="#222" d="M6.6 10.8a15.1 15.1 0 0 0 6.6 6.6l2.2-2.2c.3-.3.7-.4 1-.2 1.1.4 2.3.6 3.6.6.6 0 1 .4 1 1V20c0 .6-.4 1-1 1A17 17 0 0 1 3 4c0-.6.4-1 1-1h3.5c.6 0 1 .4 1 1 0 1.3.2 2.5.6 3.6.1.3 0 .7-.2 1z"/></svg>
    +1 201-555-0148</div>
  <div class="contact-line" style="top:168px">
    <svg width="13" height="10" viewBox="0 0 16 12"><path d="M0 0h16v12H0z" fill="#222"/><path d="M0 0l8 6 8-6" stroke="#f3a704" stroke-width="1.5" fill="none"/></svg>
    info@quillpetalloft.example</div>
  <div class="foot-social" style="top:200px"><span></span><span></span><span></span><span></span><span></span></div>

  <h4 style="left:398px">OUR SERVICES</h4>
  <ul class="service-list">
    <li>MAKEUP APPLICATION</li>
    <li>LASH EXTENSION</li>
    <li>WAXING</li>
    <li>GEL MANICURE</li>
  </ul>

  <h4 style="left:629px">OPENING HOURS</h4>
  <svg class="abs" style="left:671px;top:88px" width="58" height="58" viewBox="0 0 58 58"><circle cx="29" cy="29" r="26" fill="none" stroke="#222" stroke-width="3"/><path d="M29 14v15l10 6" stroke="#222" stroke-width="3" fill="none" stroke-linecap="round"/></svg>
  <div class="hours"><strong>9:00 AM - 7:00 PM</strong><span>Monday to Sunday</span></div>

  <h4 style="left:940px">PHOTOREEL</h4>
  <div class="feed"><span></span><span></span><span></span><span></span><span></span><span></span></div>
  <div class="feed-btn">View on Photoreel</div>

  <div class="foot-rule"></div>
  <div class="copyright">Copyright 2016 - Quill Petal Loft. All Rights Reserved.</div>
</footer>

</body>
</html>
```